I need a letterhead for a newsletter that will go out quarterly to the dentists of the 18th district. It is called "The Crestline Digest" We are in Amarillo TX and have this landmark in the photo as our most prominent feature. If it could be used, that would be cool.
This is a professional organization newsletter so the letterhead should be somewhat professional.

Target Market(s)

Dentists

Industry/Entity Type

Dental

Font styles to use
Serif

Colors

Designer to choose only greyscale colors for use in the design.

Requirements
Must have
• I want the title of "The Crestline Digest" to be the on top with the phrase "Cobalt Ridge Dental Society" written underneath.
Nice to have
• the photo incorporated could be incorporated in black and white or color along the bottom of the letterhead or with the title inside the photo.
Should not have
• I don't want it to be cartoony. I want it to be stylish and elegant and professional.

```html
<!DOCTYPE html>
<html lang="en">
<head>
<meta charset="utf-8">
<title>The Crestline Digest — Letterhead</title>
<link rel="stylesheet" href="https://fonts.googleapis.com/css2?family=Marcellus+SC&family=Questrial&family=Lato:wght@400&display=swap">
<style>
  :root {
    --brand-tone: #4a4a4a;
    --ink: #3a3a3a;
    --ink-soft: #5a5a5a;
    --photo-tone: #9a9a9a;
    --paper: #ffffff;
    --backdrop: #e4e4e4;
    --white: #ffffff;
  }
  * { box-sizing: border-box; margin: 0; padding: 0; }
  html, body { width: 1200px; height: 898px; overflow: hidden; }
  body { background: var(--backdrop); position: relative; }

  .letterhead {
    position: absolute; left: 295px; top: 18px;
    width: 610px; height: 862px;
    background: var(--paper);
    box-shadow: 0 4px 18px rgba(0, 0, 0, 0.15);
    overflow: hidden;
  }

  .masthead-shape { position: absolute; left: 0; top: 0; }
  .masthead-title {
    position: absolute; left: 150px; top: 30px; width: 340px;
    text-align: center; color: var(--white);
    font-family: "Marcellus SC", serif;
  }
  .masthead-title .name { font-size: 30px; letter-spacing: 0.5px; line-height: 1.1; }
  .masthead-title .society { font-size: 16.5px; letter-spacing: 0.4px; margin-top: 4px; }

  .contact-bar {
    position: absolute; left: 118px; right: 22px; top: 108px;
    display: flex; justify-content: space-between; align-items: center;
    padding-bottom: 5px; border-bottom: 1.5px solid var(--brand-tone);
    font-family: "Lato", sans-serif; font-size: 10.5px; color: var(--ink);
  }
  .contact-item { display: flex; align-items: center; gap: 5px; white-space: nowrap; }
  .contact-item svg { width: 11px; height: 11px; fill: var(--brand-tone); }

  .letter-body {
    position: absolute; left: 120px; top: 185px; width: 450px;
    font-family: "Questrial", sans-serif; font-size: 13.5px;
    line-height: 1.6; color: var(--ink);
  }
  .letter-body p { margin-bottom: 20px; }
  .letter-body .salutation { margin-bottom: 24px; }

  .signature { position: absolute; left: 120px; top: 612px; font-family: "Questrial", sans-serif; color: var(--ink); }
  .signature .signer { font-size: 20px; }
  .signature .role { font-size: 11.5px; color: var(--ink-soft); margin-top: 6px; }

  .footer-shape { position: absolute; left: 0; bottom: 0; }
  .footer-address {
    position: absolute; right: 18px; bottom: 38px; width: 270px;
    text-align: center; color: var(--white);
    font-family: "Lato", sans-serif; font-size: 10px; white-space: nowrap;
  }

  .landmark-photo {
    position: absolute; left: 322px; top: 640px;
    width: 252px; height: 158px;
    border: 5px solid var(--brand-tone); border-radius: 20px;
    background: var(--photo-tone);
  }
</style>
</head>
<body>
  <article class="letterhead">
    <svg class="masthead-shape" width="610" height="100" viewBox="0 0 610 100" aria-hidden="true">
      <polygon points="0,0 610,0 610,22 492,22 488,100 158,100 112,22 0,22" fill="var(--brand-tone)"/>
    </svg>
    <header class="masthead-title">
      <div class="name">The Crestline Digest</div>
      <div class="society">Cobalt Ridge Dental Society</div>
    </header>

    <div class="contact-bar">
      <span class="contact-item">
        <svg viewBox="0 0 16 16"><path d="M3 6c0-3 10-3 10 0v2h-3V6.5H6V8H3z M4 9h8l1 5H3z"/></svg>806.555.0142
      </span>
      <span class="contact-item">
        <svg viewBox="0 0 16 16"><path d="M3 6c0-3 10-3 10 0v2h-3V6.5H6V8H3z M4 9h8l1 5H3z"/></svg>806.555.0187
      </span>
      <span class="contact-item">
        <svg viewBox="0 0 16 16"><path d="M1 3h14v10H1z M2 4l6 5 6-5" fill="none" stroke="var(--brand-tone)" stroke-width="1.6"/></svg>editor@crestlinedigest.org
      </span>
      <span class="contact-item">
        <svg viewBox="0 0 16 16"><circle cx="8" cy="8" r="6.5" fill="none" stroke="var(--brand-tone)" stroke-width="1.4"/><path d="M1.5 8h13 M8 1.5c-3 3-3 10 0 13 M8 1.5c3 3 3 10 0 13" fill="none" stroke="var(--brand-tone)" stroke-width="1.1"/></svg>www.crestlinedigest.org
      </span>
    </div>

    <section class="letter-body">
      <p class="salutation">Hello Sir/Mam,</p>
      <p>Lorem ipsum dolor sit amet, consectetur adipiscing elit. Donec orci purus, luctus vitae dignissim eu, iaculis sed purus. Vivamus faucibus, ipsum nec aliquet viverra, leo mauris condimentum ligula, sit amet sagittis enim ligula quis arcu. Nam egestas tortor id nisi porttitor mattis. In tortor ante, ultricies in suscipit a, tempus non massa. Vivamus et auctor mi. Fusce vel massa nulla. Phasellus nec eros mauris, et scelerisque orci. Donec malesuada orci vitae nulla accumsan porta a id massa.</p>
      <p>Quisque accumsan iaculis magna sit amet fringilla. Maecenas consequat, magna eget tincidunt semper, odio nibh rutrum mi, id feugiat ante nisi eu risus. Vestibulum nunc orci, rhoncus a placerat in, ultricies in mi. Cras mattis varius eros, vel fringilla nisi suscipit eget. Quisque scelerisque sagittis nulla at porttitor. Mauris a justo et tellus interdum tristique. Sed id augue vitae urna euismod commodo aliquet a quam. Pellentesque arcu velit, cursus et malesuada ut, consequat et diam. Nullam erat sem, rhoncus id ullamcorper vitae, rhoncus et arcu. In ultricies ultricies nulla.</p>
    </section>

    <div class="signature">
      <div class="signer">Daniel Hale</div>
      <div class="role">Co-Founder &amp; CEO</div>
    </div>

    <svg class="footer-shape" width="610" height="62" viewBox="0 0 610 62" aria-hidden="true">
      <polygon points="0,34 300,34 318,0 610,0 610,62 0,62" fill="var(--brand-tone)"/>
    </svg>
    <div class="footer-address">415 Mesa Vista Rd, Canyon Falls, Ridge County 79000, USA</div>

    <div class="landmark-photo" role="img" aria-label="Photograph of the society's local landmark, a sandstone rock tower in a canyon"></div>
  </article>
</body>
</html>
```